Trade Show booth design

I need the following designs for my trade booth:
1. backboard design 3m Wx2mH
2. Tressle table, tablecloth front panel design 1800W x 740mmH
3. Pop-up banner. I have included our logos and some design content ideas:
Headline:
"Cleaner Classrooms. Safer Schools."
Subheadline:
"Specialist Cleaning Solutions for Education Facilities"
Key Points to Grab Attention:
Healthy Environments: Create hygienic, safe learning spaces for students and staff with our expert cleaning services.
Tailored to Your Needs: Custom cleaning plans for classrooms, labs, libraries, and sports facilities.
Affordable Excellence: Premium results without premium costs – tailored plans mean you only pay for what you need.
Safety First: All staff are trained, highly vetted, and hold current Working with Children Checks (WWCC).
Eco-Conscious Cleaning: Using non-toxic, eco-friendly products certified for health and safety.
What Schools Really Need:
Reliability: Consistent, high-quality cleaning from a trusted provider.
Cost-Effectiveness: Solutions that fit tight budgets while maintaining high standards.
Expertise: Over 30 years of experience in education facility cleaning.
Disinfection Services: Focus on high-touch areas to reduce the spread of germs and ensure peace of mind.
Visual Elements:
Images of bright, clean classrooms, a happy teacher welcoming students, or students collaborating in a spotless library.
Icons representing safety (shield), hygiene (sparkling star), and eco-friendliness (leaf).
Your logo with the tagline: "Trusted by Queensland Schools Since 1995."
Call-to-Action:
"Visit us to discuss your school’s cleaning needs and book a FREE consultation."
Include contact details: Phone: 1300 594 316 | Website: www.brightmorefacility.com.au
Target Market(s)
Education sector
Industry/Entity Type
Commercial Cleaning
Font styles to use
Other font styles liked:
- Montserrat
Look and feel

```html
<!DOCTYPE html>
<html lang="en">
<head>
<meta charset="utf-8">
<title>Brightmore Facility – Trade Show Booth</title>
<link href="https://fonts.googleapis.com/css2?family=Montserrat:wght@300;400;500;600;700;800&display=swap" rel="stylesheet">
<style>
:root{
  --navy:#0b2443;
  --navy-deep:#071a33;
  --navy-mid:#163d66;
  --cyan:#1db4ef;
  --cyan-light:#3fc8f8;
  --white:#ffffff;
  --scene-bg:#a9ccd6;
  --sheet-bg:#e3e4e6;
  --ink:#111826;
}
*{margin:0;padding:0;box-sizing:border-box}
html,body{width:1200px;height:2319px;overflow:hidden}
body{font-family:"Montserrat",sans-serif;background:var(--sheet-bg);position:relative;color:var(--white)}

.stage{position:absolute;left:0;top:0;width:1200px;height:1096px;background:var(--scene-bg)}
.sheet{position:absolute;left:0;top:1096px;width:1200px;height:1223px;background:var(--sheet-bg)}

.placed{position:absolute;transform-origin:0 0;box-shadow:0 8px 18px rgba(0,0,0,.25)}
.caption{position:absolute;font-weight:600;font-size:29px;color:var(--ink);letter-spacing:.5px;text-align:center;white-space:nowrap}

/* ---------- shared pieces ---------- */
.brand{display:flex;align-items:center;gap:8px}
.brand-dot{border-radius:50%;background:var(--cyan);flex:none}
.brand-name{font-weight:700;color:var(--white);line-height:1.05;letter-spacing:.5px}
.tagline{font-weight:700;color:var(--white);letter-spacing:.2px;white-space:nowrap}
.tagline span{color:var(--cyan)}
.photo{position:absolute}
.cta-pill{position:absolute;display:flex;align-items:center;border-radius:20px;overflow:hidden;font-weight:700;white-space:nowrap}
.cta-pill .book{background:var(--white);color:var(--navy)}
.cta-pill .free{background:var(--navy);color:var(--cyan)}

/* ---------- backboard 556 x 370 ---------- */
.backboard{width:556px;height:370px;position:relative;overflow:hidden;
  background:linear-gradient(135deg,var(--navy-deep) 0%,var(--navy-mid) 55%,var(--navy) 100%)}
.backboard .brand{position:absolute;left:30px;top:26px}
.backboard .brand-dot{width:30px;height:30px}
.backboard .brand-name{font-size:14px}
.backboard .brand-rule{width:1px;height:38px;background:rgba(255,255,255,.6);margin-left:6px}
.bb-trust{position:absolute;left:198px;top:28px;font-size:9px;line-height:1.25}
.bb-trust b{font-weight:700;display:block}
.bb-trust .since{color:var(--cyan);letter-spacing:3px;font-weight:600}
.bb-head{position:absolute;left:30px;top:88px;font-weight:800;line-height:1}
.bb-head .l1{font-size:22px;display:block}
.bb-head .l2{font-size:31px;color:var(--cyan);display:block}
.bb-sub{position:absolute;left:30px;top:153px;font-size:10px;font-weight:500}
.bb-features{position:absolute;left:28px;top:184px;width:300px;display:grid;grid-template-columns:repeat(4,1fr)}
.feature{display:flex;flex-direction:column;align-items:center;text-align:center;font-size:7.5px;font-weight:500;line-height:1.2;height:62px;padding-top:4px}
.feature + .feature{border-left:1px dashed rgba(255,255,255,.35)}
.feature:nth-child(5){border-left:none}
.feature:nth-child(-n+4){border-bottom:1px dashed rgba(255,255,255,.35)}
.feature:nth-child(n+5){padding-top:10px;height:66px}
.feat-icon{width:19px;height:19px;border-radius:50%;background:var(--cyan);display:flex;align-items:center;justify-content:center;margin-bottom:5px}
.bb-band{position:absolute;left:0;top:326px;width:350px;height:44px;background:var(--cyan)}
.bb-url{position:absolute;left:30px;top:341px;font-size:11px;font-weight:600;letter-spacing:2.6px;color:var(--navy);white-space:nowrap}
.backboard .cta-pill{left:370px;top:336px;font-size:7.5px}
.backboard .cta-pill .book{padding:4px 6px}
.backboard .cta-pill .free{padding:4px 9px 4px 7px}

/* ---------- tablecloth 556 x 228 ---------- */
.tablecloth{width:556px;height:228px;position:relative;overflow:hidden;
  background:linear-gradient(180deg,var(--navy-mid) 0%,var(--navy) 60%,var(--navy-deep) 100%)}
.tc-wave{position:absolute;left:0;top:0}
.tablecloth .brand{position:absolute;left:0;right:0;top:34px;justify-content:center}
.tablecloth .brand-dot{width:40px;height:40px}
.tablecloth .brand-name{font-size:18px}
.tablecloth .tagline{position:absolute;left:0;right:0;top:100px;text-align:center;font-size:7.5px}
.tc-url{position:absolute;left:0;right:0;top:200px;text-align:center;font-size:13px;font-weight:600;letter-spacing:4px;color:var(--navy)}

/* ---------- pop-up banner 358 x 843 ---------- */
.banner{width:358px;height:843px;position:relative;overflow:hidden;
  background:linear-gradient(180deg,var(--navy-deep) 0%,var(--navy-mid) 45%,var(--navy) 70%)}
.banner .brand{position:absolute;left:0;right:0;top:32px;justify-content:center}
.banner .brand-dot{width:40px;height:40px}
.banner .brand-name{font-size:18px}
.banner .tagline{position:absolute;left:0;right:0;top:92px;text-align:center;font-size:9px}
.pb-head{position:absolute;left:0;right:0;top:128px;text-align:center;line-height:1}
.pb-head .l1{display:block;font-weight:300;color:var(--cyan);font-size:29px}
.pb-head .l2{display:block;font-weight:800;font-size:33px;margin-top:2px}
.pb-head .l3{display:block;font-weight:800;font-size:30px;color:var(--cyan);margin-top:2px}
.pb-dots{position:absolute;left:0;right:0;top:228px;text-align:center;font-size:14px;letter-spacing:2px;font-weight:800}
.pb-sub{position:absolute;left:0;right:0;top:252px;text-align:center;font-size:15px;font-weight:600;line-height:1.25}
.pb-points{position:absolute;left:34px;top:318px;display:flex;flex-direction:column;gap:6px}
.point{width:270px;height:60px;border-radius:30px 8px 8px 30px;background:var(--cyan);display:flex;align-items:center;gap:10px;padding-left:14px;font-size:12.5px;font-weight:500;line-height:1.2}
.point-icon{width:30px;height:30px;border-radius:50%;background:var(--navy);flex:none;display:flex;align-items:center;justify-content:center}
.point-text{border-left:1px solid rgba(255,255,255,.7);padding-left:8px}
.pb-band{position:absolute;left:0;top:710px;width:358px;height:112px;background:var(--cyan)}
.pb-visit{position:absolute;left:0;right:0;top:718px;text-align:center;font-size:11px;font-weight:500;color:var(--navy)}
.banner .cta-pill{left:35px;top:735px;font-size:13.5px;letter-spacing:1px;border:1.5px solid var(--white)}
.banner .cta-pill .book{padding:2px 8px 2px 12px;font-weight:800}
.banner .cta-pill .free{padding:2px 12px 2px 10px;color:var(--white);background:var(--navy)}
.banner .cta-pill .free b{color:var(--cyan);font-weight:800}
.pb-phone{position:absolute;left:0;right:0;top:756px;display:flex;justify-content:center;align-items:center;gap:4px;font-size:28px;font-weight:700;color:var(--navy)}
.pb-url{position:absolute;left:0;right:0;top:792px;text-align:center;font-size:12.5px;font-weight:700;letter-spacing:2.5px;color:var(--navy)}
</style>
</head>
<body>

<!-- ================= BOOTH OVERVIEW ================= -->
<section class="stage">

  <div class="placed" style="left:118px;top:232px;transform:scale(1.24)">
    <div class="backboard">
      <svg class="photo" width="556" height="370" viewBox="0 0 556 370" role="img" aria-label="Photo of a bright clean classroom with a smiling teacher standing arms folded">
        <defs><linearGradient id="bbPhotoA" x1="0" y1="0" x2="0" y2="1"><stop offset="0" stop-color="#eef2f5"/><stop offset=".55" stop-color="#cfd6dc"/><stop offset="1" stop-color="#a99277"/></linearGradient></defs>
        <path d="M470 0H556V370H338V320C338 190 390 70 470 0Z" fill="url(#bbPhotoA)"/>
        <path d="M458 0C378 70 330 190 330 330" fill="none" stroke="#1db4ef" stroke-width="6"/>
        <path d="M556 0V78C520 68 500 30 516 0Z" fill="#0b2443"/>
      </svg>
      <div class="brand"><span class="brand-dot"></span><span class="brand-name">BRIGHTMORE<br>FACILITY</span><span class="brand-rule"></span></div>
      <div class="bb-trust">TRUSTED BY<b>QUEENSLAND SCHOOLS</b><span class="since">SINCE 1995</span></div>
      <h1 class="bb-head"><span class="l1">CLEANER CLASSROOMS</span><span class="l2">SAFER SCHOOLS</span></h1>
      <p class="bb-sub">Specialist Cleaning Solutions for Education Facilities</p>
      <div class="bb-features">
        <div class="feature"><span class="feat-icon"><svg width="10" height="10" viewBox="0 0 10 10"><path d="M2 5l2 2 4-4" fill="none" stroke="#fff" stroke-width="1.6"/></svg></span>Reliable<br>Service</div>
        <div class="feature"><span class="feat-icon"><svg width="10" height="10" viewBox="0 0 10 10"><path d="M2 5l2 2 4-4" fill="none" stroke="#fff" stroke-width="1.6"/></svg></span>Cost<br>Effectiveness</div>
        <div class="feature"><span class="feat-icon"><svg width="10" height="10" viewBox="0 0 10 10"><path d="M2 5l2 2 4-4" fill="none" stroke="#fff" stroke-width="1.6"/></svg></span>Disinfection<br>Services</div>
        <div class="feature"><span class="feat-icon"><svg width="10" height="10" viewBox="0 0 10 10"><path d="M2 5l2 2 4-4" fill="none" stroke="#fff" stroke-width="1.6"/></svg></span>Tailored to<br>Your Needs</div>
        <div class="feature"><span class="feat-icon"><svg width="10" height="10" viewBox="0 0 10 10"><path d="M2 5l2 2 4-4" fill="none" stroke="#fff" stroke-width="1.6"/></svg></span>Expertise<br>Over<br>30 year</div>
        <div class="feature"><span class="feat-icon"><svg width="10" height="10" viewBox="0 0 10 10"><path d="M2 5l2 2 4-4" fill="none" stroke="#fff" stroke-width="1.6"/></svg></span>Healthy<br>Environments</div>
        <div class="feature"><span class="feat-icon"><svg width="10" height="10" viewBox="0 0 10 10"><path d="M2 5l2 2 4-4" fill="none" stroke="#fff" stroke-width="1.6"/></svg></span>Affordable<br>Excellence</div>
        <div class="feature"><span class="feat-icon"><svg width="10" height="10" viewBox="0 0 10 10"><path d="M5 1l3 1.2v2.6C8 7 6.6 8.4 5 9 3.4 8.4 2 7 2 4.8V2.2z" fill="#fff"/></svg></span>Safety<br>First</div>
      </div>
      <div class="bb-band"></div>
      <div class="bb-url">www.brightmorefacility.com.au</div>
      <div class="cta-pill"><span class="book">BOOK A</span><span class="free">FREE CONSULTATION</span></div>
    </div>
  </div>

  <div class="placed" style="left:200px;top:716px;transform:scale(0.97)">
    <div class="tablecloth">
      <svg class="tc-wave" width="556" height="228" viewBox="0 0 556 228" aria-hidden="true">
        <path d="M0 178C70 162 130 186 200 172S320 150 380 145 480 150 556 168V228H0Z" fill="#1db4ef"/>
        <path d="M0 192C90 172 170 198 250 184S380 160 440 158 510 165 556 178V228H0Z" fill="#3fc8f8" opacity=".6"/>
      </svg>
      <div class="brand"><span class="brand-dot"></span><span class="brand-name">BRIGHTMORE<br>FACILITY</span></div>
      <div class="tagline">TRUSTED BY QUEENSLAND SCHOOLS <span>SINCE 1995</span></div>
      <div class="tc-url">www.brightmorefacility.com.au</div>
    </div>
  </div>

  <div class="placed" style="left:838px;top:245px;transform:scale(0.67)">
    <div class="banner">
      <div class="brand"><span class="brand-dot"></span><span class="brand-name">BRIGHTMORE<br>FACILITY</span></div>
      <div class="tagline">TRUSTED BY QUEENSLAND SCHOOLS <span>SINCE 1995</span></div>
      <h2 class="pb-head"><span class="l1">CLEANER</span><span class="l2">CLASSROOMS</span><span class="l3">SAFER SCHOOLS</span></h2>
      <div class="pb-dots">•••••</div>
      <p class="pb-sub">Specialist Cleaning Solutions for<br>Education Facilities</p>
      <div class="photo" style="left:262px;top:296px;width:96px;height:250px;background:linear-gradient(180deg,#c9d3dc,#2d3f78 60%,#d7dde3)" role="img" aria-label="Photo of a cleaner in an apron mopping the floor"></div>
      <div class="pb-points">
        <div class="point"><span class="point-icon"><svg width="14" height="14" viewBox="0 0 14 14"><path d="M3 7l3 3 5-6" fill="none" stroke="#fff" stroke-width="2"/></svg></span><span class="point-text">Over 30 years of<br>expertise in<br>commercial cleaning.</span></div>
        <div class="point"><span class="point-icon"><svg width="14" height="14" viewBox="0 0 14 14"><path d="M3 7l3 3 5-6" fill="none" stroke="#fff" stroke-width="2"/></svg></span><span class="point-text">Trusted by schools,<br>universities, and TAFEs<br>across Queensland.</span></div>
        <div class="point"><span class="point-icon"><svg width="14" height="14" viewBox="0 0 14 14"><path d="M3 7l3 3 5-6" fill="none" stroke="#fff" stroke-width="2"/></svg></span><span class="point-text">100% Carbon Neutral<br>and Eco-Certified<br>Services.</span></div>
      </div>
      <svg class="photo" style="left:0;top:540px" width="358" height="303" viewBox="0 0 358 303" role="img" aria-label="Photo of a bright clean classroom with a teacher standing between the desks">
        <path d="M0 120C60 60 130 20 250 25 300 28 330 40 358 20V303H0Z" fill="#d8dee3"/>
        <path d="M0 180H358V303H0Z" fill="#b3977a" opacity=".55"/>
      </svg>
      <div class="pb-band"></div>
      <div class="pb-visit">Visit us to discuss your school's cleaning needs &amp;</div>
      <div class="cta-pill"><span class="book">BOOK A</span><span class="free"><b>FREE</b> CONSULTATION</span></div>
      <div class="pb-phone"><svg width="20" height="20" viewBox="0 0 20 20"><circle cx="10" cy="10" r="9" fill="none" stroke="#0b2443" stroke-width="2.2"/><path d="M7 5.5l2 2-1 1.3c.7 1.4 1.6 2.3 3 3l1.3-1 2 2-1.3 1.5C9.8 14 6 10.2 5.5 6.8z" fill="#0b2443"/></svg>1300 594 316</div>
      <div class="pb-url">www.brightmorefacility.com.au</div>
    </div>
  </div>

</section>

<!-- ================= FLAT DESIGN SHEET ================= -->
<section class="sheet">

  <div class="placed" style="left:105px;top:132px">
    <div class="banner">
      <div class="brand"><span class="brand-dot"></span><span class="brand-name">BRIGHTMORE<br>FACILITY</span></div>
      <div class="tagline">TRUSTED BY QUEENSLAND SCHOOLS <span>SINCE 1995</span></div>
      <h2 class="pb-head"><span class="l1">CLEANER</span><span class="l2">CLASSROOMS</span><span class="l3">SAFER SCHOOLS</span></h2>
      <div class="pb-dots">•••••</div>
      <p class="pb-sub">Specialist Cleaning Solutions for<br>Education Facilities</p>
      <div class="photo" style="left:262px;top:296px;width:96px;height:250px;background:linear-gradient(180deg,#c9d3dc,#2d3f78 60%,#d7dde3)" role="img" aria-label="Photo of a cleaner in an apron mopping the floor"></div>
      <div class="pb-points">
        <div class="point"><span class="point-icon"><svg width="14" height="14" viewBox="0 0 14 14"><path d="M3 7l3 3 5-6" fill="none" stroke="#fff" stroke-width="2"/></svg></span><span class="point-text">Over 30 years of<br>expertise in<br>commercial cleaning.</span></div>
        <div class="point"><span class="point-icon"><svg width="14" height="14" viewBox="0 0 14 14"><path d="M3 7l3 3 5-6" fill="none" stroke="#fff" stroke-width="2"/></svg></span><span class="point-text">Trusted by schools,<br>universities, and TAFEs<br>across Queensland.</span></div>
        <div class="point"><span class="point-icon"><svg width="14" height="14" viewBox="0 0 14 14"><path d="M3 7l3 3 5-6" fill="none" stroke="#fff" stroke-width="2"/></svg></span><span class="point-text">100% Carbon Neutral<br>and Eco-Certified<br>Services.</span></div>
      </div>
      <svg class="photo" style="left:0;top:540px" width="358" height="303" viewBox="0 0 358 303" role="img" aria-label="Photo of a bright clean classroom with a teacher standing between the desks">
        <path d="M0 120C60 60 130 20 250 25 300 28 330 40 358 20V303H0Z" fill="#d8dee3"/>
        <path d="M0 180H358V303H0Z" fill="#b3977a" opacity=".55"/>
      </svg>
      <div class="pb-band"></div>
      <div class="pb-visit">Visit us to discuss your school's cleaning needs &amp;</div>
      <div class="cta-pill"><span class="book">BOOK A</span><span class="free"><b>FREE</b> CONSULTATION</span></div>
      <div class="pb-phone"><svg width="20" height="20" viewBox="0 0 20 20"><circle cx="10" cy="10" r="9" fill="none" stroke="#0b2443" stroke-width="2.2"/><path d="M7 5.5l2 2-1 1.3c.7 1.4 1.6 2.3 3 3l1.3-1 2 2-1.3 1.5C9.8 14 6 10.2 5.5 6.8z" fill="#0b2443"/></svg>1300 594 316</div>
      <div class="pb-url">www.brightmorefacility.com.au</div>
    </div>
  </div>

  <div class="placed" style="left:538px;top:132px">
    <div class="backboard">
      <svg class="photo" width="556" height="370" viewBox="0 0 556 370" role="img" aria-label="Photo of a bright clean classroom with a smiling teacher standing arms folded">
        <defs><linearGradient id="bbPhotoB" x1="0" y1="0" x2="0" y2="1"><stop offset="0" stop-color="#eef2f5"/><stop offset=".55" stop-color="#cfd6dc"/><stop offset="1" stop-color="#a99277"/></linearGradient></defs>
        <path d="M470 0H556V370H338V320C338 190 390 70 470 0Z" fill="url(#bbPhotoB)"/>
        <path d="M458 0C378 70 330 190 330 330" fill="none" stroke="#1db4ef" stroke-width="6"/>
        <path d="M556 0V78C520 68 500 30 516 0Z" fill="#0b2443"/>
      </svg>
      <div class="brand"><span class="brand-dot"></span><span class="brand-name">BRIGHTMORE<br>FACILITY</span><span class="brand-rule"></span></div>
      <div class="bb-trust">TRUSTED BY<b>QUEENSLAND SCHOOLS</b><span class="since">SINCE 1995</span></div>
      <h1 class="bb-head"><span class="l1">CLEANER CLASSROOMS</span><span class="l2">SAFER SCHOOLS</span></h1>
      <p class="bb-sub">Specialist Cleaning Solutions for Education Facilities</p>
      <div class="bb-features">
        <div class="feature"><span class="feat-icon"><svg width="10" height="10" viewBox="0 0 10 10"><path d="M2 5l2 2 4-4" fill="none" stroke="#fff" stroke-width="1.6"/></svg></span>Reliable<br>Service</div>
        <div class="feature"><span class="feat-icon"><svg width="10" height="10" viewBox="0 0 10 10"><path d="M2 5l2 2 4-4" fill="none" stroke="#fff" stroke-width="1.6"/></svg></span>Cost<br>Effectiveness</div>
        <div class="feature"><span class="feat-icon"><svg width="10" height="10" viewBox="0 0 10 10"><path d="M2 5l2 2 4-4" fill="none" stroke="#fff" stroke-width="1.6"/></svg></span>Disinfection<br>Services</div>
        <div class="feature"><span class="feat-icon"><svg width="10" height="10" viewBox="0 0 10 10"><path d="M2 5l2 2 4-4" fill="none" stroke="#fff" stroke-width="1.6"/></svg></span>Tailored to<br>Your Needs</div>
        <div class="feature"><span class="feat-icon"><svg width="10" height="10" viewBox="0 0 10 10"><path d="M2 5l2 2 4-4" fill="none" stroke="#fff" stroke-width="1.6"/></svg></span>Expertise<br>Over<br>30 year</div>
        <div class="feature"><span class="feat-icon"><svg width="10" height="10" viewBox="0 0 10 10"><path d="M2 5l2 2 4-4" fill="none" stroke="#fff" stroke-width="1.6"/></svg></span>Healthy<br>Environments</div>
        <div class="feature"><span class="feat-icon"><svg width="10" height="10" viewBox="0 0 10 10"><path d="M2 5l2 2 4-4" fill="none" stroke="#fff" stroke-width="1.6"/></svg></span>Affordable<br>Excellence</div>
        <div class="feature"><span class="feat-icon"><svg width="10" height="10" viewBox="0 0 10 10"><path d="M5 1l3 1.2v2.6C8 7 6.6 8.4 5 9 3.4 8.4 2 7 2 4.8V2.2z" fill="#fff"/></svg></span>Safety<br>First</div>
      </div>
      <div class="bb-band"></div>
      <div class="bb-url">www.brightmorefacility.com.au</div>
      <div class="cta-pill"><span class="book">BOOK A</span><span class="free">FREE CONSULTATION</span></div>
    </div>
  </div>

  <div class="caption" style="left:538px;width:556px;top:564px">BACKBOARD DESIGN</div>

  <div class="placed" style="left:538px;top:723px">
    <div class="tablecloth">
      <svg class="tc-wave" width="556" height="228" viewBox="0 0 556 228" aria-hidden="true">
        <path d="M0 178C70 162 130 186 200 172S320 150 380 145 480 150 556 168V228H0Z" fill="#1db4ef"/>
        <path d="M0 192C90 172 170 198 250 184S380 160 440 158 510 165 556 178V228H0Z" fill="#3fc8f8" opacity=".6"/>
      </svg>
      <div class="brand"><span class="brand-dot"></span><span class="brand-name">BRIGHTMORE<br>FACILITY</span></div>
      <div class="tagline">TRUSTED BY QUEENSLAND SCHOOLS <span>SINCE 1995</span></div>
      <div class="tc-url">www.brightmorefacility.com.au</div>
    </div>
  </div>

  <div class="caption" style="left:105px;width:358px;top:1027px">POP-UP BANNER</div>
  <div class="caption" style="left:538px;width:556px;top:1027px">TABLECLOTH FRONT PANEL DESIGN</div>

</section>

</body>
</html>
```